Brell Stone Company Business Cards

Front and Back Business Card - logo and text setup - cool design. I need workable photoshop or illustrator files so I can setup each employee card with design that is created
Updates

Hi everyone, thank you for the great entries. Please no more white and blue cards - there are so many already - black and silver only now please. thanks!

Target Market(s)

Construction Industry - Facility Managers

Industry/Entity Type

Construction

Contact Information for Business Card

I really like contemporary simplistic looks - clean neat....not opposed to seeing some black backrounds

Requirements
Must have
• Logo/website address with design on front only - www.brellstone-example.com (logo attached)
• Back:
• Name/Title/Company Address/Phone/email address
Nice to have
• Cool design
Should not have
• Nothing gimmicky like Fire or Water - since we are a Fire Protection company - it has all been done

```html
<!DOCTYPE html>
<html lang="en">
<head>
<meta charset="utf-8">
<title>Brell Stone Company Business Cards</title>
<link href="https://fonts.googleapis.com/css2?family=Roboto:wght@400;500;700;900&display=swap" rel="stylesheet">
<style>
  :root {
    --backdrop: #3b332f;
    --card-black: #1b1b1d;
    --silver: #d6d6d6;
    --silver-bright: #ececec;
    --silver-mid: #a9a9a9;
    --silver-dark: #6e6e70;
    --text-silver: #c4c4c4;
    --rule-silver: #5c5c5e;
  }
  * { margin: 0; padding: 0; box-sizing: border-box; }
  html, body { width: 1200px; height: 716px; overflow: hidden; }
  body {
    background: var(--backdrop);
    font-family: "Roboto", Arial, sans-serif;
    position: relative;
  }
  .card {
    position: absolute;
    top: 210px;
    width: 520px;
    height: 297px;
    background: var(--card-black);
    box-shadow: 0 10px 30px rgba(0,0,0,.45);
    overflow: hidden;
  }
  .card-front {
    left: 50px;
    display: flex;
    align-items: center;
    justify-content: center;
  }
  .front-wordmark {
    font-weight: 900;
    font-size: 58px;
    color: var(--silver);
    letter-spacing: -1px;
  }
  .card-back { left: 630px; }
  .back-wordmark {
    position: absolute;
    top: 48px;
    right: 36px;
    font-weight: 900;
    font-size: 40px;
    color: var(--silver-bright);
    letter-spacing: -1px;
  }
  .person {
    position: absolute;
    top: 74px;
    left: 34px;
  }
  .person-name {
    font-weight: 700;
    font-size: 19px;
    color: var(--silver-bright);
  }
  .person-title {
    font-size: 13px;
    color: var(--silver-mid);
    margin-top: 2px;
  }
  .divider {
    position: absolute;
    top: 134px;
    left: 180px;
    right: 36px;
    height: 1px;
    background: var(--rule-silver);
  }
  .contacts {
    position: absolute;
    top: 140px;
    left: 34px;
    list-style: none;
    font-size: 13px;
    color: var(--text-silver);
    line-height: 19px;
  }
  .contacts li { display: flex; align-items: center; gap: 7px; }
  .contacts svg { width: 11px; height: 11px; fill: var(--silver); flex: none; }
  .address {
    position: absolute;
    right: 36px;
    bottom: 38px;
    text-align: right;
    font-size: 13px;
    line-height: 18px;
    color: var(--text-silver);
  }
  .address .web { letter-spacing: 1.5px; }
  .band {
    position: absolute;
    bottom: 0;
    left: 0;
    right: 0;
    height: 10px;
    display: flex;
  }
  .band-dark { width: 58%; background: var(--silver-dark); }
  .band-light { flex: 1; background: var(--silver); margin-left: 4px; }
</style>
</head>
<body>
  <section class="card card-front" aria-label="Card front">
    <div class="front-wordmark">Brell Stone</div>
  </section>

  <section class="card card-back" aria-label="Card back">
    <div class="person">
      <div class="person-name">Alex Morgan</div>
      <div class="person-title">CEO/Founder</div>
    </div>
    <div class="back-wordmark">Brell Stone</div>
    <div class="divider"></div>
    <ul class="contacts">
      <li><svg viewBox="0 0 12 12"><path d="M3 1l2 2.5-1.2 1.2c.6 1.3 1.6 2.3 2.9 2.9L7.9 6.4 10.5 8.5 9 11C5 10.5 1.5 7 1 3z"/></svg>(555) 014-2087</li>
      <li><svg viewBox="0 0 12 12"><rect x="3" y="1" width="6" height="3"/><rect x="1" y="5" width="10" height="5" rx="1"/></svg>(555) 014-2088</li>
      <li><svg viewBox="0 0 12 12"><path d="M1 2.5h10v7H1z M1 2.5l5 4 5-4" stroke="#1b1b1d" stroke-width=".8"/></svg>info@brellstone-example.com</li>
    </ul>
    <div class="address">
      <div>48 Harbor Point Drive</div>
      <div>Lakeview, NY 10501</div>
      <div class="web">www.brellstone-example.com</div>
    </div>
    <div class="band"><div class="band-dark"></div><div class="band-light"></div></div>
  </section>
</body>
</html>
```